The Harlow Reserve Web Site design

I need a web design for my luxury range of Terry Toweling and Spa Accessories for luxury upmarket hotels and Spas. I have a catalog that sets the mood and tone I am looking for. I need a website design that shows off the look and feel of this luxury range while working back to the catalog look and feel. Its all about Upmarket and Luxury. I will be using the website as a reference site and as a site that customers can purchase off.
The Logo is attached as is the catalog. I don't mind changing the color of the Logo to match the website. However I would prefer to keep the font of that logo.

http://thegallerydesk.pixvault-example.com/p504729381
Please can you try and access this link. The Harlow Reserve
Name Greta. Email greta@vellumsupply-example.com.au. Password Harlow.
These images are to be used for shopping page and please use the close up details of texture as background on pages and use those texture details and close ups for banners

Please note the look and feel has to be very upmarket and super luxury. Ficus is on mood and not on retail.
Have a look at the mood on the following websites
Www.gracefulretreats-example.com
And yourcosyseasidecabin-example.com
That one is retail .mi don't want retail focus but it's very clean. And simple and colors are good
Updates

Please rebook brief. I have added some important detail. Thanks

Relook brief. I have added,important detail. Thanks

Target Market(s)

Corporate buyers
This is not for retail selling to consumers
Price it's viewed only after secure login

Industry/Entity Type

Shopping

Colors
acd037
cadf82
fbc995
fce7d3
faa54b

Requirements
Must have
• Luxury. Think luxury. Very high end yet modern like the catalogue
Use banners on home page
Should not have
• Don't use the blue as the main color. It's too cheap.
No products on home page

```html
<!DOCTYPE html>
<html lang="en">
<head>
<meta charset="utf-8">
<title>The Harlow Reserve</title>
<link href="https://fonts.googleapis.com/css2?family=Rye&family=Josefin+Slab:wght@300;400&family=Zilla+Slab:wght@400;500&family=Roboto:wght@400&display=swap" rel="stylesheet">
<style>
  :root{
    --green:#acd037;
    --green-light:#cadf82;
    --green-dark:#8aa82a;
    --peach:#fbc995;
    --cream:#fce7d3;
    --orange:#faa54b;
    --ink:#1a1a1a;
    --white:#ffffff;
    --footer:#050505;
  }
  *{box-sizing:border-box;margin:0;padding:0}
  html,body{width:1200px;height:675px;overflow:hidden;background:#000}
  .page{position:relative;width:1200px;height:675px;overflow:hidden;font-family:"Zilla Slab",serif}

  .scene{position:absolute}
  .scene-bedroom{left:0;top:0;width:631px;height:627px;
    background:
      radial-gradient(ellipse 190px 110px at 250px 170px,rgba(236,232,226,.95) 0%,rgba(200,196,190,.6) 55%,rgba(0,0,0,0) 100%),
      radial-gradient(ellipse 130px 100px at 520px 180px,rgba(220,218,214,.8) 0%,rgba(0,0,0,0) 100%),
      radial-gradient(ellipse 420px 120px at 300px 440px,rgba(230,230,228,.85) 0%,rgba(150,150,150,.4) 60%,rgba(0,0,0,0) 100%),
      linear-gradient(180deg,#0c0c0c 0%,#1a1918 30%,#3a3937 58%,#6d6d6b 75%,#555553 100%)}
  .scene-towels{left:631px;top:0;width:569px;height:434px;
    background:
      linear-gradient(180deg,rgba(0,0,0,0) 70%,rgba(40,38,34,.35) 100%),
      linear-gradient(90deg,#5e5a53 0%,#7a746a 14%,#f3f2ee 20%,#fbfbf9 30%,#d9d7d2 36%,#6a655c 42%,#837c71 55%,#6c675e 62%,#f1f0ec 72%,#fcfcfa 82%,#d5d3cd 88%,#6a645b 93%,#524e47 100%)}
  .scene-shore{left:631px;top:434px;width:569px;height:193px;
    background:
      linear-gradient(170deg,rgba(0,0,0,0) 45%,rgba(226,223,215,.95) 62%,#cfcbc2 100%),
      linear-gradient(90deg,#171411 0%,#3d2f1f 30%,#5a4328 50%,#2e4b55 75%,#3e6a78 100%)}
  .thumb{position:absolute;border:4px solid var(--green)}
  .thumb-bed{left:527px;top:125px;width:192px;height:279px;
    background:
      radial-gradient(ellipse 90px 70px at 110px 90px,rgba(245,244,240,.95) 0%,rgba(0,0,0,0) 100%),
      linear-gradient(175deg,#2a2825 0%,#4a4844 18%,#d8d6d1 38%,#a9a6a0 62%,#605e59 85%,#3a3835 100%)}
  .thumb-chair{left:658px;top:46px;width:121px;height:175px;
    background:
      radial-gradient(ellipse 45px 55px at 65px 95px,rgba(226,222,214,.95) 0%,rgba(0,0,0,0) 100%),
      linear-gradient(180deg,#4a3d30 0%,#5e4e3c 45%,#3b3128 80%,#2a231d 100%)}

  .brand{position:absolute;left:71px;top:0;width:277px;height:59px;background:var(--orange);
    display:flex;align-items:center;justify-content:center;
    font-family:"Rye",serif;color:var(--white);font-size:23px;letter-spacing:.3px}

  .hero{position:absolute;left:0;top:266px;width:506px;height:230px;background:rgba(255,255,255,.42)}
  .hero-kicker{position:absolute;left:120px;top:2px;font-family:"Josefin Slab",serif;font-weight:400;font-size:35px;letter-spacing:.6px;color:var(--ink)}
  .hero-title{position:absolute;left:68px;top:26px;font-family:"Josefin Slab",serif;font-weight:300;font-size:92px;letter-spacing:15px;color:var(--ink);line-height:1}
  .hero-copy{position:absolute;left:71px;top:113px;width:360px;font-size:14.5px;line-height:16.5px;color:var(--ink)}
  .hero-cta{position:absolute;left:73px;top:180px;width:169px;height:31px}
  .hero-cta span{position:absolute;left:44px;top:4px;font-family:"Zilla Slab",serif;font-size:20px;letter-spacing:1.5px;color:var(--ink)}

  .signup-form{position:absolute;left:819px;top:258px;width:260px;height:183px;background:var(--green);padding:21px 16px 0 16px}
  .field{display:flex;align-items:center;justify-content:space-between;height:27.5px}
  .field label{font-size:14px;color:#2b2b2b}
  .field input{width:160px;height:21px;border:1px solid #b9cf6a;background:var(--green-light)}
  .submit{position:absolute;right:16px;top:135px;width:71px;height:25px;border:0;background:var(--green-dark);
    color:var(--white);font-family:"Zilla Slab",serif;font-size:13px}

  .quick-tabs{position:absolute;left:1141px;top:242px;width:59px;height:218px;background:var(--orange);
    display:flex;flex-direction:column}
  .tab{flex:1;display:flex;flex-direction:column;align-items:center;justify-content:center;
    font-family:"Roboto",sans-serif;font-size:11px;line-height:14px;color:var(--white);text-align:center;
    border-bottom:1px solid rgba(255,255,255,.7)}
  .tab:last-child{border-bottom:0}
  .tab svg{margin-bottom:4px}

  .site-footer{position:absolute;left:0;top:627px;width:1200px;height:48px;background:var(--footer);border-top:1px solid #444}
  .footer-nav{position:absolute;left:72px;top:11px;display:flex;font-size:16px;color:var(--white)}
  .footer-nav span:nth-child(1){width:174px}
  .footer-nav span:nth-child(2){width:128px}
  .social{position:absolute;left:507px;top:10px;display:flex;gap:7px}
  .social i{display:block;width:18px;height:18px;border-radius:50%;background:var(--peach)}
  .contact{position:absolute;left:822px;top:9px;font-family:"Roboto",sans-serif;font-size:9.5px;line-height:14px;color:#e8e8e8;font-style:normal}
</style>
</head>
<body>
<main class="page">
  <div class="scene scene-bedroom" role="img" aria-label="Photograph of a dim bedroom with white pillows and a quilted throw"></div>
  <div class="scene scene-towels" role="img" aria-label="Photograph of white terry towels hanging on a weathered wooden wall"></div>
  <div class="scene scene-shore" role="img" aria-label="Photograph of a towel-draped lounger by a rocky shoreline"></div>
  <div class="thumb thumb-bed" role="img" aria-label="Photograph of a made bed with white linens"></div>
  <div class="thumb thumb-chair" role="img" aria-label="Photograph of a knitted throw on an armchair"></div>

  <header class="brand">The Harlow Reserve</header>

  <section class="hero">
    <p class="hero-kicker">Wrap Yourself in</p>
    <h1 class="hero-title">Luxury</h1>
    <p class="hero-copy">Here at The Harlow Reserve we deliver the finest in cotton towels, loungewear, and bath accessories to ensure that your bath and spa collection</p>
    <a class="hero-cta" href="#">
      <svg width="169" height="31" viewBox="0 0 169 31"><polygon points="0,0 169,0 169,31 0,31 12,15.5" fill="#acd037"/></svg>
      <span>SIGN IN</span>
    </a>
  </section>

  <form class="signup-form">
    <div class="field"><label>Name</label><input type="text"></div>
    <div class="field"><label>Email</label><input type="text"></div>
    <div class="field"><label>Address</label><input type="text"></div>
    <div class="field"><label>City</label><input type="text"></div>
    <button class="submit" type="button">Submit</button>
  </form>

  <nav class="quick-tabs">
    <div class="tab">
      <svg width="22" height="18" viewBox="0 0 22 18" fill="none" stroke="#fff" stroke-width="2"><path d="M7 7 L11 1 L15 7"/><path d="M1 7 H21 L18 17 H4 Z" fill="#fff"/></svg>
      0 items<br>$0.00
    </div>
    <div class="tab">
      <svg width="16" height="22" viewBox="0 0 16 22"><path d="M4 10 V6 a4 4 0 0 1 8 0 V10" fill="none" stroke="#fff" stroke-width="2.2"/><rect x="1" y="10" width="14" height="11" rx="1" fill="#fff"/><rect x="7" y="13" width="2" height="5" fill="#faa54b"/></svg>
      Sign Up
    </div>
    <div class="tab">
      <svg width="22" height="16" viewBox="0 0 22 16"><rect x="0" y="0" width="22" height="16" fill="#fff"/><path d="M0 0 L11 9 L22 0" fill="none" stroke="#faa54b" stroke-width="1.5"/></svg>
      Contact
    </div>
  </nav>

  <footer class="site-footer">
    <div class="footer-nav"><span>Sign in or Register</span><span>My Harlow</span><span>My Wish List</span></div>
    <div class="social" aria-label="Social links"><i></i><i></i><i></i><i></i><i></i></div>
    <address class="contact">
      48 Linden Row, Harbor City, FL 30418<br>
      Phone: (555) 014-2290, Fax: (555) 014-7731, &nbsp;&nbsp;hello@theharlowreserve-example.com
    </address>
  </footer>
</main>
</body>
</html>
```